New National Dermatology Group needs a business card!

We need a business card for our new national company that has 3 brands within the business:
Lumora Clinics Australia, Tessaly Clinics Australia and Corvane Clinics Australia.
We help people access dermatology services close to home throughout Australia.
We need a business card that has:
all 3 logos on it,
Our websites (there are three, listed above)
Our email (there are three, listed above)
The location of our first clinic: 41 Willow Rd Parramatta (this can then be changed for each location as required)

```html
<!DOCTYPE html>
<html lang="en">
<head>
<meta charset="utf-8">
<title>Clinics Australia – Business Card</title>
<link rel="stylesheet" href="https://fonts.googleapis.com/css2?family=Arimo:wght@400&display=swap">
<style>
  :root {
    --bg: #c4c4c4;
    --paper: #ffffff;
    --ink: #222222;
    --rule: #d4d4d4;
    --brown: #7a3e1d;
    --green: #22b04b;
    --orange: #f4842b;
    --text-font: "Arimo", sans-serif;
  }
  * { box-sizing: border-box; margin: 0; padding: 0; }
  html, body { width: 1200px; height: 800px; overflow: hidden; }
  body {
    background: var(--bg);
    display: flex;
    align-items: center;
    justify-content: center;
    gap: 40px;
    font-family: var(--text-font);
  }
  .card {
    width: 540px;
    height: 310px;
    box-shadow: 0 8px 24px rgba(0,0,0,0.25);
    overflow: hidden;
  }

  /* Front side */
  .card--front {
    background: var(--paper);
    display: flex;
    padding: 18px 22px;
  }
  .brand-list, .contact-list {
    display: flex;
    flex-direction: column;
  }
  .brand-list { width: 250px; }
  .contact-list { flex: 1; padding-left: 22px; }
  .brand, .contact {
    flex: 1;
    display: flex;
    flex-direction: column;
    justify-content: center;
  }
  .brand + .brand, .contact + .contact { border-top: 1px solid var(--rule); }

  .brand-name {
    font-family: var(--text-font);
    font-weight: 400;
    font-size: 17px;
    line-height: 1.2;
    white-space: nowrap;
  }
  .brand--corvane .brand-name { color: var(--brown); }
  .brand--lumora .brand-name { color: var(--green); }
  .brand--tessaly .brand-name { color: var(--orange); }

  .contact { font-size: 13px; color: var(--ink); gap: 4px; }
  .contact__row { display: flex; align-items: center; gap: 7px; white-space: nowrap; }
  .contact__row svg { width: 12px; height: 12px; flex: none; color: var(--accent); }
  .contact--corvane { --accent: var(--brown); }
  .contact--lumora { --accent: var(--green); }
  .contact--tessaly { --accent: var(--orange); }
  .contact__domain { color: var(--accent); }

  /* Back side */
  .card--back {
    display: flex;
    flex-direction: column;
    gap: 3px;
    background: var(--paper);
  }
  .band {
    flex: 1;
    display: flex;
    align-items: center;
    justify-content: center;
    color: var(--paper);
  }
  .band--corvane { background: var(--brown); }
  .band--lumora { background: var(--green); }
  .band--tessaly { background: var(--orange); }
  .band .brand-name { font-size: 26px; color: var(--paper); }
</style>
</head>
<body>

<svg width="0" height="0" style="position:absolute" aria-hidden="true">
  <defs>
    <symbol id="icon-mail" viewBox="0 0 12 12">
      <rect x="0.5" y="2" width="11" height="8" fill="currentColor"/>
      <path d="M0.5 2 L6 6.5 L11.5 2" fill="none" stroke="#fff" stroke-width="1"/>
    </symbol>
    <symbol id="icon-globe" viewBox="0 0 12 12">
      <circle cx="6" cy="6" r="5.5" fill="currentColor"/>
      <g fill="none" stroke="#fff" stroke-width="0.7">
        <ellipse cx="6" cy="6" rx="2.3" ry="5.5"/>
        <line x1="0.5" y1="6" x2="11.5" y2="6"/>
        <line x1="1.3" y1="3.5" x2="10.7" y2="3.5"/>
        <line x1="1.3" y1="8.5" x2="10.7" y2="8.5"/>
      </g>
    </symbol>
    <symbol id="icon-pin" viewBox="0 0 12 12">
      <path d="M6 11.5 C3 8 2 6.5 2 4.5 A4 4 0 0 1 10 4.5 C10 6.5 9 8 6 11.5 Z" fill="currentColor"/>
      <circle cx="6" cy="4.5" r="1.5" fill="#fff"/>
    </symbol>
  </defs>
</svg>

<section class="card card--front" aria-label="Business card front">
  <div class="brand-list">
    <div class="brand brand--corvane"><p class="brand-name">Corvane Clinics Australia</p></div>
    <div class="brand brand--lumora"><p class="brand-name">Lumora Clinics Australia</p></div>
    <div class="brand brand--tessaly"><p class="brand-name">Tessaly Clinics Australia</p></div>
  </div>

  <div class="contact-list">
    <div class="contact contact--corvane">
      <p class="contact__row"><svg><use href="#icon-mail"/></svg>info@corvaneclinics.com</p>
      <p class="contact__row"><svg><use href="#icon-globe"/></svg><span>www.<span class="contact__domain">corvaneclinics</span>.com</span></p>
      <p class="contact__row"><svg><use href="#icon-pin"/></svg>41 Willow Rd Parramatta</p>
    </div>
    <div class="contact contact--lumora">
      <p class="contact__row"><svg><use href="#icon-mail"/></svg>info@lumoraclinics.com</p>
      <p class="contact__row"><svg><use href="#icon-globe"/></svg><span>www.<span class="contact__domain">lumoraclinics</span>.com</span></p>
      <p class="contact__row"><svg><use href="#icon-pin"/></svg>41 Willow Rd Parramatta</p>
    </div>
    <div class="contact contact--tessaly">
      <p class="contact__row"><svg><use href="#icon-mail"/></svg>info@tessalyclinics.com</p>
      <p class="contact__row"><svg><use href="#icon-globe"/></svg><span>www.<span class="contact__domain">tessalyclinics</span>.com</span></p>
      <p class="contact__row"><svg><use href="#icon-pin"/></svg>41 Willow Rd Parramatta</p>
    </div>
  </div>
</section>

<section class="card card--back" aria-label="Business card back">
  <div class="band band--corvane"><p class="brand-name">Corvane Clinics Australia</p></div>
  <div class="band band--lumora"><p class="brand-name">Lumora Clinics Australia</p></div>
  <div class="band band--tessaly"><p class="brand-name">Tessaly Clinics Australia</p></div>
</section>

</body>
</html>
```